ELsewhen website redesign to provide information about experiential workshops, film work and other

We need a redesign of our website elsewhen.org. We conduct experiential workshops of discovery and transformation for individuals and organizations. We need the website to reflect the full extent of ELsewhen programs, and be an information hub for ELsewhen workshops and communities as they develop.

The attached documents contain information about the organization - it's brandbook, copy for web pages, a website layout and a couple of images.

The site is for individuals and companies looking to promote and be change to make a difference. It should be warm, welcoming, and create excitement around the concepts and the ability to discover a new way of being in the world. We are about creating communities around the globe who will embody play, freedom, curiosity and expanded possibilities. We are creating a space for this to happen, both physically (workshops) and online.

We will be on either a SquareSpace, but mos tlikely a Weebly plaform.

Please look at the current site at www.elsewhen.org

Target Market(s)

Initially, are target market will be baby boomers, but will expand to include millennials and students.

Coding

Coded - Design and coding required

Number of Pages Required

5+ page

Requirements
Must have
• The colors, logo and fonts from the brand book.
Nice to have
• Complimentary use of brand colors to create an attractive presentation and energy

```html
<!DOCTYPE html>
<html lang="en">
<head>
<meta charset="utf-8">
<title>ELsewhen — Workshops of Discovery</title>
<link href="https://fonts.googleapis.com/css2?family=Lato:wght@400;700;900&display=swap" rel="stylesheet">
<style>
:root{
  --ink:#1c1c1c;
  --dark:#222222;
  --mauve:#a3737c;
  --orange:#f0622d;
  --amber:#f5a63d;
  --green:#78b47f;
  --mint:#6ac18c;
  --sky:#9fd0d6;
  --field:#eeeeee;
  --field-line:#d8d8d8;
  --white:#ffffff;
  --muted:#555555;
  --symbol:#e6e1e2;
}
*{margin:0;padding:0;box-sizing:border-box}
html,body{width:1200px;height:3232px;overflow:hidden}
body{font-family:'Lato',sans-serif;color:var(--ink);background:var(--white);position:relative}
.abs{position:absolute}
/* hero */
.hero{left:0;top:0;width:1200px;height:664px;background:linear-gradient(180deg,#3a3128 0%,#5e4d3d 40%,#6b5a49 65%,#3f372f 100%)}
.brand{font-weight:900;color:var(--white);font-size:32px;letter-spacing:3px;display:flex;align-items:center;gap:12px}
.brand .mark{width:16px;height:16px;background:currentColor}
.btn{display:flex;align-items:center;justify-content:center;color:var(--white);font-weight:700;font-size:15px;height:40px;border-radius:2px;letter-spacing:.3px}
.btn-capture{left:786px;top:32px;width:160px;background:var(--mint)}
.btn-login{left:960px;top:32px;width:166px;background:var(--amber)}
.nav{left:75px;top:103px;width:1050px;height:48px;border-top:1px solid rgba(255,255,255,.7);border-bottom:1px solid rgba(255,255,255,.7);display:flex;justify-content:space-between;align-items:center;padding:0 20px}
.nav span{color:var(--white);font-weight:700;font-size:14px}
.cta{left:75px;top:571px;width:1050px;height:190px;display:flex}
.cta div{flex:1;background:var(--dark);color:var(--white);text-align:center;padding-top:34px}
.cta div+div{background:#1a1a1a}
.cta h2{font-size:34px;font-weight:700;line-height:1.12;text-transform:uppercase}
.cta svg{margin-top:14px}
/* discover */
.discover{left:0;top:815px;width:1200px;text-align:center;font-size:26px;font-weight:700;line-height:1.25;text-transform:uppercase}
.logo-dark{left:0;top:908px;width:1200px;justify-content:center;color:var(--ink);font-size:34px}
.path{left:0;top:960px}
.node{width:86px;height:86px;border-radius:50%;display:flex;align-items:center;justify-content:center}
.label{width:220px;text-align:center;font-weight:700;font-size:16px;line-height:1.3}
/* vision */
.vision{left:0;top:1271px;width:1200px;height:382px;background:var(--mauve)}
.vision-text{left:75px;top:46px;width:510px;color:var(--white)}
.band-title{font-size:26px;font-weight:700;text-transform:uppercase;margin-bottom:18px;letter-spacing:.5px}
.band-copy{font-size:14px;line-height:1.75}
.band-copy+.band-copy{margin-top:18px}
.vision-photo{left:616px;top:0;width:584px;height:382px;background:linear-gradient(135deg,#4d6a36,#6f8650 45%,#4a3f35 78%,#2c2622)}
/* what we do */
.wwd-title{left:0;top:1708px;width:1200px;text-align:center;font-size:26px;font-weight:700}
.wwd-sub{left:0;top:1770px;width:1200px;text-align:center;color:var(--orange);font-weight:700;font-size:14px}
.wwd-copy{left:80px;top:1795px;width:1040px;text-align:center;font-size:14px;line-height:1.85;color:var(--muted)}
.wwd-lead{left:0;top:1897px;width:1200px;text-align:center;font-weight:700;font-size:14px;color:var(--muted)}
.wwd-lead b{color:var(--orange)}
.move{width:200px;text-align:center;top:1950px}
.move .symbol{width:104px;height:96px;margin:0 auto;background:var(--symbol)}
.move p{margin-top:14px;font-weight:700;font-size:16px}
/* stirring */
.stir{left:0;top:2158px;width:1200px;height:406px;background:var(--mauve)}
.stir-photo{left:0;top:0;width:586px;height:406px;background:linear-gradient(160deg,#5f5d58,#7f7b74 40%,#3d3b37 80%,#1f1e1c)}
.stir-text{left:614px;top:44px;width:510px;color:var(--white)}
/* community */
.comm-title{left:0;top:2615px;width:1200px;text-align:center;font-size:26px;font-weight:700}
.comm-copy{left:0;top:2668px;width:1200px;text-align:center;font-size:14px;line-height:1.85;color:var(--muted)}
.field{background:var(--field);border:1px solid var(--field-line);font-size:13px;font-weight:700;color:#555;padding:0 16px;display:flex;align-items:center;text-transform:uppercase}
.field.msg{align-items:flex-start;padding-top:18px}
.submit{left:614px;top:2886px;width:422px;height:54px;background:var(--orange);color:var(--white);font-weight:900;font-size:16px;display:flex;align-items:center;justify-content:center}
/* footer */
.footer{left:0;top:2994px;width:1200px;height:238px;background:var(--dark);color:#cfcfcf}
.footer .brand{left:75px;top:74px;font-size:26px;color:#e0e0e0}
.copyright{left:75px;top:122px;font-size:12px;line-height:1.75;color:#bbbbbb}
.f-head{font-size:14px;font-weight:700;color:var(--white);text-transform:uppercase}
.f-links{font-size:12px;line-height:2.6;color:#d0d0d0}
.email-field{left:656px;top:73px;width:228px;height:38px;background:#3a3a3a;color:#bbb;font-size:13px;display:flex;align-items:center;padding:0 14px}
.signup{left:803px;top:122px;width:80px;height:38px;background:var(--mint);color:var(--white);font-weight:700;font-size:13px;display:flex;align-items:center;justify-content:center}
.social{left:926px;top:72px;display:flex;gap:12px}
.social span{width:22px;height:22px;border-radius:50%;background:#d8d8d8}
</style>
</head>
<body>

<section class="hero abs" role="img" aria-label="Photo of workshop participants seated together in a warm, wood-panelled room"></section>
<div class="brand abs" style="left:75px;top:36px"><span class="mark"></span>ELSEWHEN</div>
<div class="btn btn-capture abs">EMAIL CAPTURE</div>
<div class="btn btn-login abs">MEMBER LOGIN</div>
<nav class="nav abs">
  <span>HOME</span><span>ABOUT US</span><span>WORKSHOPS</span><span>ELSEWHEN PROJECTS</span><span>FILMS</span><span>STORE &amp; RESOURCES</span><span>COMMUNITY</span><span>CONTACT US</span>
</nav>
<div class="cta abs">
  <div>
    <h2>What world do we<br>want to live in?</h2>
    <svg width="28" height="28" viewBox="0 0 28 28"><path d="M3 14h18M13 5l9 9-9 9" stroke="#f5a63d" stroke-width="5" fill="none" stroke-linecap="round" stroke-linejoin="round"/></svg>
  </div>
  <div>
    <h2>What kind of life do you<br>want to create?</h2>
    <svg width="28" height="28" viewBox="0 0 28 28"><path d="M3 14h18M13 5l9 9-9 9" stroke="#f5a63d" stroke-width="5" fill="none" stroke-linecap="round" stroke-linejoin="round"/></svg>
  </div>
</div>

<h2 class="discover abs">Discover an opportunity to live a more dynamic<br>and meaningful life</h2>
<div class="brand logo-dark abs"><span class="mark"></span>ELSEWHEN</div>

<svg class="path abs" width="1200" height="150" viewBox="0 0 1200 150">
  <path d="M172 68 C260 68,300 136,386 136 C470 136,520 68,601 68 C690 68,730 136,814 136 C900 136,940 68,1027 68" stroke="#777" stroke-width="2" stroke-dasharray="3 5" fill="none"/>
</svg>

<div class="node abs" style="left:129px;top:985px;background:var(--green)">
  <svg width="40" height="40" viewBox="0 0 40 40" fill="#fff"><circle cx="20" cy="9" r="5"/><path d="M12 30c0-8 4-14 8-14s8 6 8 14z"/><rect x="6" y="29" width="28" height="4" rx="2"/></svg>
</div>
<div class="node abs" style="left:343px;top:1053px;background:var(--amber)">
  <svg width="44" height="40" viewBox="0 0 44 40" fill="#fff"><circle cx="22" cy="12" r="5"/><circle cx="11" cy="16" r="4"/><circle cx="33" cy="16" r="4"/><path d="M14 32c0-7 4-12 8-12s8 5 8 12z"/><path d="M4 31c0-5 3-9 7-9 2 0 3 1 4 2-2 2-3 5-3 7z"/><path d="M40 31c0-5-3-9-7-9-2 0-3 1-4 2 2 2 3 5 3 7z"/></svg>
</div>
<div class="node abs" style="left:558px;top:985px;background:var(--sky)">
  <svg width="42" height="36" viewBox="0 0 42 36" fill="#fff"><ellipse cx="21" cy="15" rx="18" ry="13"/><path d="M9 24l-3 10 11-7z"/></svg>
</div>
<div class="node abs" style="left:771px;top:1053px;background:var(--orange)">
  <svg width="36" height="42" viewBox="0 0 36 42" fill="#fff"><circle cx="18" cy="7" r="5"/><path d="M4 10l10 8v22h8V18l10-8-3-3-9 7h-4L7 7z"/></svg>
</div>
<div class="node abs" style="left:984px;top:985px;background:var(--ink)">
  <svg width="30" height="40" viewBox="0 0 30 40" fill="none" stroke="#fff" stroke-width="3"><path d="M15 3a11 11 0 0 0-6 20v6h12v-6A11 11 0 0 0 15 3z"/><path d="M10 34h10M12 38h6"/></svg>
</div>

<p class="label abs" style="left:62px;top:1088px">Moves Energy</p>
<p class="label abs" style="left:276px;top:1156px">Creates Opportunities<br>for Connecting</p>
<p class="label abs" style="left:491px;top:1088px">Supports Conscious<br>Evolution</p>
<p class="label abs" style="left:704px;top:1156px">Deepens Experience<br>of Life</p>
<p class="label abs" style="left:917px;top:1088px">Provides Opportunities for<br>Collaboration &amp; Creation</p>

<section class="vision abs">
  <div class="vision-text abs">
    <h3 class="band-title">Vision</h3>
    <p class="band-copy">We envision a world in which all people and communities can challenge and break free from stories that no longer serve us. We believe that solutions to contemporary challenges will emerge from a place of curiosity, love and connection.</p>
    <p class="band-copy">Through inspiration, conscious reflection, and collaboration, we take responsibility for the world we are manifesting, and we can discover and create new possibilities for the lives and the society we desire to build.</p>
  </div>
  <div class="vision-photo abs" role="img" aria-label="Photo of two workshop facilitators seated on a sofa before tall windows with green trees"></div>
</section>

<h2 class="wwd-title abs">WHAT WE DO</h2>
<p class="wwd-sub abs">ELSEWHEN LIFE:</p>
<p class="wwd-copy abs">Elsewhen Life is a workshop designed to re-engage you with life. Through interactive exercises and personal exploration, you are taken on a journey that ultimately leaves you experiencing life as a Creator. You will learn to see beliefs and patterns that hold you back in work and relationships as well as a path to transforming the story of your life.</p>
<p class="wwd-lead abs"><b>ELSEWHEN LIFE</b> IS A 2-3 DAY WORKSHOP EXPERIENCED IN 5 MOVEMENTS:</p>

<div class="move abs" style="left:73px">
  <div class="symbol" role="img" aria-label="Movement symbol for Curiosity"></div>
  <p>Curiosity</p>
</div>
<div class="move abs" style="left:287px">
  <div class="symbol" role="img" aria-label="Movement symbol for Awareness"></div>
  <p>Awareness</p>
</div>
<div class="move abs" style="left:501px">
  <div class="symbol" role="img" aria-label="Movement symbol for Owning the Creation"></div>
  <p>Owning the Creation</p>
</div>
<div class="move abs" style="left:714px">
  <div class="symbol" role="img" aria-label="Movement symbol for Reimagining"></div>
  <p>Reimagining</p>
</div>
<div class="move abs" style="left:927px">
  <div class="symbol" role="img" aria-label="Movement symbol for Manifesting"></div>
  <p>Manifesting</p>
</div>

<section class="stir abs">
  <div class="stir-photo abs" role="img" aria-label="Photo of costumed performers and a gathered crowd in front of a weathered barn wall hung with artworks"></div>
  <div class="stir-text abs">
    <h3 class="band-title">Stirring the Still</h3>
    <p class="band-copy">The Stirring the Still workshop—an extension of the documentary of the same name—is an experiential process to transform participants into stirrers of the status quo within themselves, to enhance their relationships with others, and to change the environments in which they exist—and ultimately society—for the better.</p>
    <p class="band-copy">This workshop experience challenges us all to understand the narratives we live within, to look at our current roles in society, and to decide what role we will play to create a more humane, just and peaceful world, for all. It all starts with our willingness to stir the “stillness” of the status quo.</p>
  </div>
</section>

<h2 class="comm-title abs">IN YOUR COMMUNITY</h2>
<p class="comm-copy abs">Bring Elsewhen or the Stirring the Still workshop to your community. We would love to hear from you.<br>Please fill out the brief form here</p>
<div class="field abs" style="left:164px;top:2753px;width:422px;height:54px">Name</div>
<div class="field abs" style="left:164px;top:2819px;width:422px;height:54px">Email Address</div>
<div class="field abs" style="left:164px;top:2886px;width:422px;height:54px">Phone No</div>
<div class="field msg abs" style="left:614px;top:2753px;width:422px;height:120px">Message</div>
<div class="submit abs">SUBMIT NOW</div>

<footer class="footer abs">
  <div class="brand abs"><span class="mark"></span>ELSEWHEN</div>
  <p class="copyright abs">Copyright © 2018. Company Name<br>All Right Reserved</p>
  <p class="f-head abs" style="left:341px;top:36px">Site Map</p>
  <p class="f-links abs" style="left:341px;top:56px">About Us<br>Workshops<br>Elsewhen Projects<br>Films</p>
  <p class="f-links abs" style="left:508px;top:56px">Store &amp; Resources<br>Community<br>Contact Us</p>
  <p class="f-head abs" style="left:656px;top:36px">Email Sign Up</p>
  <div class="email-field abs">Enter Email Address</div>
  <div class="signup abs">SIGN UP</div>
  <p class="f-head abs" style="left:926px;top:36px">Follow Us</p>
  <div class="social abs"><span></span><span></span><span></span><span></span><span></span><span></span></div>
</footer>

</body>
</html>
```